Business Card Design

We like to use greens as you will see in our logo (but not TOO much green). We are a Dental Clinic in a somewhat eccentric community. We do not like the dated sharp designs which we see many dentists use. We're looking for something bright and fresh while still maintaining the integrity of the profession. Elegance is not necessarily what we are going for... we need for the design to be "mature" but also up-lifting.

See our logo.
Updates

Project Deadline Extended
Reason: We have 5 designs which we like. But we'd like to see a few more before committing to a design.

Project Deadline Extended
Reason: We are awaiting revisions to this project. We are still welcoming designs while we wait to see if designers are able to provide to us the revisions we require in order to proceed with a selection.

Target Market(s)

Younger families - ages late 20's to early 40's

Industry/Entity Type

Business

Contact Information for Business Card

Corwel T. Banfry DDS 2730 W. Halvert Rd. Ste. 7 Royal Oak, MI 48391 (248)555-0174 FX (248)555-0189 info@BrightwellDentalCareMi.com BrigthwellDentalCareMi.com on the back of the card we need an appointment reminder (For____ Date___ Time____) with "If you are unable to keep your appointment, kindly give 48 hours notice" at the bottom. No use of teeth in the design. DOUBLE SIDED DESIGN

Requirements
Should not have
• The use of pictures of teeth

```html
<!DOCTYPE html>
<html lang="en">
<head>
<meta charset="utf-8">
<title>Brightwell Dental Care – Business Card</title>
<link href="https://fonts.googleapis.com/css2?family=Cinzel:wght@500&family=Open+Sans:ital,wght@0,400;0,600;0,700;1,400&display=swap" rel="stylesheet">
<style>
  :root {
    --green-dark: #1d6b34;
    --green-light: #7cc527;
    --ink: #2b2b2b;
    --paper: #ffffff;
    --backdrop: #eeece8;
    --rule: #555555;
  }
  * { box-sizing: border-box; margin: 0; padding: 0; }
  html, body {
    width: 1200px; height: 1179px; overflow: hidden;
    background: var(--backdrop);
    font-family: "Open Sans", Arial, sans-serif;
    color: var(--ink);
  }
  .canvas { position: relative; width: 1200px; height: 1179px; }

  .card {
    position: absolute;
    width: 917px; height: 526px;
    background: var(--paper);
    overflow: hidden;
    box-shadow: 0 2px 8px rgba(0,0,0,.18);
  }
  .card--front { left: 27px; top: 34px; }
  .card--back  { left: 255px; top: 599px; border: 1px solid #9a9a9a; }

  /* Front */
  .accent-field {
    position: absolute; left: 0; top: 230px; width: 917px; height: 296px;
    background: linear-gradient(150deg,
      rgba(255,255,255,0) 42%,
      rgba(124,197,39,.85) 47%,
      var(--green-dark) 54%,
      var(--green-dark) 100%);
  }
  .brand { position: absolute; left: 88px; top: 98px; width: 380px; }
  .brand__name {
    font-weight: 700; font-size: 62px; line-height: 1;
    color: var(--green-dark); letter-spacing: -1px;
  }
  .brand__rule { height: 3px; background: var(--green-light); margin: 14px 0 8px; }
  .brand__tag {
    font-weight: 400; font-size: 40px; line-height: 1;
    color: var(--green-dark); letter-spacing: 1px;
  }
  .doctor { position: absolute; left: 651px; top: 52px; }
  .doctor__name { font-weight: 700; font-size: 30px; color: var(--green-dark); line-height: 1.2; }
  .doctor__title { font-size: 22px; color: var(--ink); line-height: 1.3; }
  .address {
    position: absolute; left: 88px; top: 322px;
    font-size: 20px; line-height: 31px; font-style: normal;
  }
  .contacts {
    position: absolute; right: 34px; top: 360px;
    list-style: none; text-align: right; color: #fff; font-size: 21px;
  }
  .contacts li { height: 39px; display: flex; justify-content: flex-end; align-items: center; gap: 8px; }
  .contacts svg { width: 18px; height: 18px; fill: #fff; }

  /* Back */
  .appt__title {
    position: absolute; left: 0; right: 0; top: 88px; text-align: center;
    font-family: "Cinzel", Georgia, serif; font-size: 33px; font-weight: 500;
    color: var(--green-dark);
  }
  .field { position: absolute; font-size: 24px; line-height: 1; }
  .dots { position: absolute; border-bottom: 2px dotted var(--rule); height: 0; }
  .slot { position: absolute; border: 2px solid #444; border-radius: 4px; height: 35px; }
  .day { position: absolute; top: 379px; font-size: 24px; font-weight: 600; }
  .day-box { position: absolute; top: 375px; width: 55px; height: 34px; border: 2px solid #444; border-radius: 4px; }
  .notice {
    position: absolute; left: 0; right: 0; top: 455px; text-align: center;
    font-style: italic; font-size: 23px;
  }
</style>
</head>
<body>
<main class="canvas">

  <section class="card card--front" aria-label="Business card front">
    <div class="accent-field" role="img" aria-label="Decorative green wave band across the lower card"></div>

    <div class="brand">
      <div class="brand__name">Brightwell</div>
      <div class="brand__rule"></div>
      <div class="brand__tag">DENTAL CARE</div>
    </div>

    <div class="doctor">
      <div class="doctor__name">Corwel T. Banfry</div>
      <div class="doctor__title">DDS</div>
    </div>

    <address class="address">
      2730 W. Halvert Rd.<br>Ste. 7 Royal Oak, MI 48391
    </address>

    <ul class="contacts">
      <li><svg viewBox="0 0 24 24"><path d="M6.6 10.8a15 15 0 0 0 6.6 6.6l2.2-2.2c.3-.3.7-.4 1-.2 1.1.4 2.3.6 3.6.6.6 0 1 .4 1 1V20c0 .6-.4 1-1 1A17 17 0 0 1 3 4c0-.6.4-1 1-1h3.5c.6 0 1 .4 1 1 0 1.3.2 2.5.6 3.6.1.3 0 .7-.2 1z"/></svg>(248)555-0174</li>
      <li><svg viewBox="0 0 24 24"><path d="M6 3h10v5H6zM4 9h16a2 2 0 0 1 2 2v6h-4v4H6v-4H2v-6a2 2 0 0 1 2-2zm4 8v2h8v-2z"/></svg>(248)555-0189</li>
      <li><svg viewBox="0 0 24 24"><path d="M12 2a10 10 0 1 0 0 20 10 10 0 0 0 0-20zm6.9 6h-3a15 15 0 0 0-1.3-3.9A8 8 0 0 1 18.9 8zM12 4c.8 1.2 1.5 2.5 1.9 4h-3.8c.4-1.5 1.1-2.8 1.9-4zM4.3 14a8 8 0 0 1 0-4h3.4a16 16 0 0 0 0 4zm.8 2h3a15 15 0 0 0 1.3 3.9A8 8 0 0 1 5.1 16zm3-8h-3a8 8 0 0 1 4.3-3.9C8.8 5.3 8.4 6.6 8.1 8zM12 20c-.8-1.2-1.5-2.5-1.9-4h3.8c-.4 1.5-1.1 2.8-1.9 4zm2.3-6H9.7a14 14 0 0 1 0-4h4.6a14 14 0 0 1 0 4zm.3 5.9c.6-1.2 1-2.5 1.3-3.9h3a8 8 0 0 1-4.3 3.9zm1.7-5.9a16 16 0 0 0 0-4h3.4a8 8 0 0 1 0 4z"/></svg>BrigthwellDentalCareMi.com</li>
      <li><svg viewBox="0 0 24 24"><path d="M2 5h20v14H2zm2 2v.5l8 5 8-5V7zm0 2.8V17h16V9.8l-8 5z"/></svg>info@BrightwellDentalCareMi.com</li>
    </ul>
  </section>

  <section class="card card--back" aria-label="Appointment reminder card back">
    <h2 class="appt__title">YOUR APPOINTMENT</h2>

    <span class="field" style="left:72px; top:163px;">Name :</span>
    <span class="dots" style="left:175px; width:665px; top:182px;"></span>

    <span class="field" style="left:72px; top:227px;">Date :</span>
    <span class="dots" style="left:175px; width:230px; top:246px;"></span>
    <span class="field" style="left:412px; top:227px;">Time :</span>
    <span class="dots" style="left:493px; width:242px; top:246px;"></span>
    <span class="field" style="left:741px; top:227px;">am / pm</span>

    <span class="field" style="left:72px; top:292px;">Next Appointment</span>
    <span class="slot" style="left:326px; top:285px; width:163px;"></span>
    <span class="slot" style="left:503px; top:285px; width:164px;"></span>
    <span class="slot" style="left:679px; top:285px; width:164px;"></span>

    <span class="day" style="left:69px;">MON</span><span class="day-box" style="left:145px;"></span>
    <span class="day" style="left:212px;">TUE</span><span class="day-box" style="left:274px;"></span>
    <span class="day" style="left:342px;">WED</span><span class="day-box" style="left:413px;"></span>
    <span class="day" style="left:480px;">THU</span><span class="day-box" style="left:547px;"></span>
    <span class="day" style="left:613px;">FRI</span><span class="day-box" style="left:666px;"></span>
    <span class="day" style="left:733px;">SAT</span><span class="day-box" style="left:793px;"></span>

    <p class="notice">If you are unable to keep your appointment, kindly give 48 hours notice</p>
  </section>

</main>
</body>
</html>
```